military training website velmotrail.com

I have a website that someone designed I am not happy with. It looks like the designer did not have the artistic ability to make a quality product. the power points are ideas that I had for the website. the business proposal was designed by someone else, and I like the style and font used, the website should reflect this document. The main part of the website should be informational with few pictures, maybe some background images behind or off to the side of the text. I would like to include a generic map with four locations marked, which, when you hover the cursor over them, show a picture of the actual location with an artistic effect or blurred so it doesn't look like a plivora atlas snip, and a picture that resembles what services are offered there, along with the text description, pictures can be found in the documents I attached, also can be stock images. this is outlined in the power points roughly.
Want to have the side menu of the major topics, or at the top, and scroll down a single page to find all of the information we have to offer

Target Market(s)

Special operations military

Industry/Entity Type

military

Coding

Coded - Design and coding required

Number of Pages Required

1 page

Other font styles liked:
• Agency FB

Colors
0054AA
0677BA
7BADD7
CADEEF
E8F1F8
00AB8E
00BBA5
67D7C9
C6EFE9
E9F9F6

Requirements
Must have
• interactive "map"
Nice to have
• professional design features to make it look like a professional website, not a beginner designer

```html
<!DOCTYPE html>
<html lang="en">
<head>
<meta charset="utf-8">
<title>Velmotrail — Master The Mission</title>
<link href="https://fonts.googleapis.com/css2?family=Michroma&family=Montserrat:wght@400;500;600;700&display=swap" rel="stylesheet">
<style>
:root{
  --blue:#0054AA;
  --blue-mid:#0677BA;
  --blue-soft:#7BADD7;
  --blue-pale:#CADEEF;
  --blue-mist:#E8F1F8;
  --ink:#111;
  --text:#444;
  --white:#fff;
  --black:#000;
}
*{box-sizing:border-box;margin:0;padding:0}
html,body{width:1200px;height:4710px;overflow:hidden}
body{position:relative;font-family:'Montserrat',sans-serif;color:var(--text);background:var(--white)}
.abs{position:absolute}
.display{font-family:'Michroma',sans-serif;color:var(--ink);font-weight:400}
.btn{position:absolute;display:flex;align-items:center;justify-content:center;background:var(--blue);color:var(--white);font-weight:600;font-size:15px;border-radius:24px}

/* header */
.site-header{position:absolute;left:0;top:0;width:1200px;height:85px;background:var(--white);z-index:5}
.brand-card{position:absolute;left:97px;top:0;width:158px;height:143px;background:var(--white);border-radius:0 0 8px 8px;z-index:6;display:flex;flex-direction:column;align-items:center;justify-content:center;gap:8px}
.brand-dot{width:54px;height:54px;border-radius:50%;background:var(--blue)}
.brand-name{font-family:'Montserrat',sans-serif;font-weight:700;font-size:14px;color:var(--blue);letter-spacing:1px}
.nav{position:absolute;left:305px;top:34px;display:flex;gap:29px;font-size:12px;color:#333;letter-spacing:.3px}
.nav-cta{left:916px;top:20px;width:171px;height:43px;font-size:15px}

/* hero */
.hero{position:absolute;left:0;top:85px;width:1200px;height:600px;overflow:hidden}
.hero-photo{position:absolute;inset:0;background:linear-gradient(160deg,#5f7585 0%,#8a9aa2 35%,#6e7c68 65%,#4b5a4c 100%)}
.hero-title{position:absolute;left:0;top:165px;width:1200px;text-align:center;color:var(--white);font-size:70px;letter-spacing:2px}
.hero-tag{position:absolute;left:0;top:260px;width:1200px;text-align:center;color:var(--white);font-size:50px}
.hero-wave{position:absolute;left:0;bottom:0}

/* mission */
.mission-title{left:0;top:745px;width:1200px;text-align:center;font-size:38px}
.mission-text{left:150px;top:815px;width:900px;text-align:center;font-size:19px;line-height:36px;color:#333}

/* provide */
.provide{left:0;top:1015px;width:1200px;height:890px;background:linear-gradient(180deg,#d3e1ec,#c5d6e4)}
.provide-title{left:0;top:1093px;width:1200px;text-align:center;font-size:40px}
.provide-text{left:170px;top:1165px;width:860px;text-align:center;font-size:13.5px;line-height:29px;color:#444}
.card{position:absolute;top:1352px;width:307px;height:443px;background:var(--white);border-radius:6px;text-align:center}
.card-num{width:126px;height:126px;border-radius:50%;background:var(--blue);color:var(--white);margin:31px auto 0;display:flex;align-items:center;justify-content:center;font-family:'Michroma',sans-serif;font-size:52px}
.card p{font-size:13.5px;line-height:29px;padding:26px 18px 0;color:#555}
.card .more{font-size:14px;font-weight:700;color:var(--blue);display:block;margin-top:0}
.arrow{position:absolute;width:56px;height:56px}

/* qualifications */
.qual-photo{left:115px;top:2010px;width:436px;height:436px;border-radius:50%;border:10px solid var(--blue);background:radial-gradient(circle at 40% 60%,#8a7e63,#3a3628 60%,#1c1b16)}
.qual-title{left:598px;top:2030px;font-size:38px;line-height:54px}
.qual-text{left:598px;top:2155px;width:440px;font-size:14px;line-height:30px;color:#444}
.qual-btn{left:600px;top:2395px;width:171px;height:43px}

/* map */
.map-band{left:2px;top:2552px;width:1198px;height:736px;background:linear-gradient(180deg,#d1dfea,#c4d5e3)}
.map-title{left:0;top:2638px;width:1200px;text-align:center;font-size:40px}
.map-frame{left:154px;top:2724px;width:893px;height:436px;border:2px solid var(--blue);border-radius:6px;background:radial-gradient(ellipse at 30% 40%,#d9a85c,#b98335 55%,#8c5e22);overflow:hidden}
.pin{position:absolute}
.map-tip{left:465px;top:2790px;width:113px;height:115px;background:var(--blue);color:var(--white);font-size:9.5px;line-height:18px;padding:6px 8px;font-weight:500}

/* gallery */
.gallery-title{left:0;top:3380px;width:1200px;text-align:center;font-size:40px}
.shot{position:absolute;top:3470px;width:232px;height:287px;border-radius:4px}

/* contact */
.contact-photo{left:84px;top:3870px;width:488px;height:430px;background:linear-gradient(180deg,#c98a3c 0%,#7a5430 45%,#2d2118 100%)}
.contact-frame{left:771px;top:3920px;width:316px;height:220px;border:2px solid var(--blue)}
.contact-card{left:465px;top:3935px;width:600px;height:375px;background:var(--white);box-shadow:0 4px 18px rgba(0,0,0,.12)}
.contact-title{position:absolute;left:28px;top:60px;font-size:30px;font-weight:700;color:var(--ink);font-family:'Michroma',sans-serif}
.field{position:absolute;border-bottom:1.5px solid #999;font-size:12px;color:#777;padding-bottom:18px}
.send{position:absolute;left:516px;top:255px;width:64px;height:64px;border-radius:50%;background:var(--blue);display:flex;align-items:center;justify-content:center}

/* footer */
.footer{left:0;top:4150px;width:1200px;height:560px;background:var(--black)}
.footer-brand{left:0;top:4390px;width:1200px;display:flex;flex-direction:column;align-items:center;gap:10px}
.footer-dot{width:70px;height:70px;border-radius:50%;background:var(--blue-mid)}
.footer-name{color:var(--white);font-weight:700;font-size:16px;letter-spacing:1px}
.socials{left:520px;top:4550px;width:160px;display:flex;justify-content:space-between}
.social{width:20px;height:20px;border-radius:50%;background:var(--white)}
.footer-nav{left:0;top:4603px;width:1200px;display:flex;justify-content:center;gap:36px;color:var(--white);font-size:14px}
.footer-rule{left:113px;top:4660px;width:977px;height:1px;background:#aaa}
.copyright{left:0;top:4676px;width:1200px;text-align:center;color:var(--white);font-size:13px}
</style>
</head>
<body>

<header class="site-header">
  <nav class="nav">
    <span>MISSION</span><span>WHAT WE PROVIDE</span><span>MAP</span><span>QUALIFICATIONS</span><span>CONTACT</span><span>GALLERY</span>
  </nav>
  <a class="btn nav-cta">Contact Us</a>
</header>
<div class="brand-card"><span class="brand-dot"></span><span class="brand-name">VELMOTRAIL</span></div>

<section class="hero">
  <div class="hero-photo" role="img" aria-label="Parachutist in freefall above farmland seen from an aircraft ramp"></div>
  <h1 class="hero-title display" style="color:#fff">VELMOTRAIL</h1>
  <p class="hero-tag display" style="color:#fff">Master The Mission</p>
  <svg class="hero-wave" width="1200" height="70" viewBox="0 0 1200 70">
    <path d="M0 55 C250 20 450 15 650 35 C850 55 1000 55 1200 45 L1200 70 L0 70Z" fill="var(--blue)"/>
    <path d="M0 68 C250 35 450 30 650 48 C850 66 1000 66 1200 60 L1200 70 L0 70Z" fill="#fff"/>
  </svg>
</section>

<h2 class="abs display mission-title">Mission</h2>
<p class="abs mission-text">Pioneering realistic training within a strategic theater across the full spectrum of SOF capabilities, liberating warriors from the shackles of logistical burdens and unleashing their full potential to vanquish adversaries</p>

<section class="abs provide" role="img" aria-label="Faint background of tiltrotor aircraft on an airfield"></section>
<h2 class="abs display provide-title">What We Provide</h2>
<p class="abs provide-text">At Velmo Trail, we draw upon years of invaluable experience gained from training at SOF facilities worldwide. Our journey has culminated in the creation of an all-encompassing training site tailored to meet the exacting needs of SOF operators. We</p>
<a class="btn" style="left:512px;top:1252px;width:172px;height:43px">Read More</a>

<svg class="arrow" style="left:19px;top:1557px" viewBox="0 0 56 56"><circle cx="28" cy="28" r="25" fill="none" stroke="#666" stroke-width="3"/><path d="M32 16 L20 28 L32 40" fill="none" stroke="#666" stroke-width="3"/></svg>
<div class="card" style="left:110px"><div class="card-num">1</div><p>Precision Marksmanship: Utilizing Tier 1 level instructors alongside seasoned local tactical shooting experts, our comprehensive programs incorporate practice with both steel and paper targets, conducted across multiple shooting locations for varied training<span class="more">Read More</span></p></div>
<div class="card" style="left:445px"><div class="card-num">2</div><p>Immersive Scenarios: We have transformed a former Soviet military stronghold into a dynamic training environment, meticulously furnished with explosives, pyrotechnics, and a live Opposition Force for verisimilar assault scenarios. Underground lays<span class="more">Read More</span></p></div>
<div class="card" style="left:782px"><div class="card-num">3</div><p>Airfield Dominance: With a sprawling 7000ft runway available, we provide an expansive canvas for a myriad of airfield operations, including seizures, static line operations, military free fall, and helicopter insertion and extraction techniques.<span class="more">Read More</span></p></div>
<svg class="arrow" style="left:1125px;top:1557px" viewBox="0 0 56 56"><circle cx="28" cy="28" r="25" fill="none" stroke="var(--blue)" stroke-width="3"/><path d="M24 16 L36 28 L24 40" fill="none" stroke="var(--blue)" stroke-width="3"/></svg>

<div class="abs qual-photo" role="img" aria-label="Night scene of an operator beside a tiltrotor aircraft and vehicle on a flight line"></div>
<h2 class="abs display qual-title">Qualifications<br>Summary</h2>
<p class="abs qual-text">The founders of Velmo Trail OÜ bring forth a wealth of experience and expertise to the table. A former USAF Combat Controller, with nearly a decade of service in Europe; and a highly esteemed former Estonian Special Operator who graduated BUDs and Ranger School, with a proven track record of business success in Estonia. Together, we are steadfast in our dedication to delivering world-class</p>
<a class="btn qual-btn">Read More</a>

<section class="abs map-band" role="img" aria-label="Faint background of aircraft on a runway"></section>
<h2 class="abs display map-title">Map</h2>
<div class="abs map-frame" role="img" aria-label="Interactive parchment-style world map with training site markers">
  <svg class="pin" style="left:204px;top:55px" width="22" height="30" viewBox="0 0 22 30"><path d="M11 29C11 29 2 17 2 11a9 9 0 0118 0c0 6-9 18-9 18z" fill="#111"/><circle cx="11" cy="11" r="3.5" fill="#d9a85c"/></svg>
  <svg class="pin" style="left:282px;top:55px" width="22" height="30" viewBox="0 0 22 30"><path d="M11 29C11 29 2 17 2 11a9 9 0 0118 0c0 6-9 18-9 18z" fill="var(--blue-mid)"/><circle cx="11" cy="11" r="3.5" fill="#fff"/></svg>
  <svg class="pin" style="left:246px;top:90px" width="22" height="30" viewBox="0 0 22 30"><path d="M11 29C11 29 2 17 2 11a9 9 0 0118 0c0 6-9 18-9 18z" fill="#111"/><circle cx="11" cy="11" r="3.5" fill="#d9a85c"/></svg>
  <svg class="pin" style="left:320px;top:210px" width="22" height="30" viewBox="0 0 22 30"><path d="M11 29C11 29 2 17 2 11a9 9 0 0118 0c0 6-9 18-9 18z" fill="#111"/><circle cx="11" cy="11" r="3.5" fill="#d9a85c"/></svg>
</div>
<div class="abs map-tip">Site - 1<br>Village Complex<br>Tunnel System<br>MFF<br>HLZ<br>OPFOR LODGING</div>

<h2 class="abs display gallery-title">Our Gallery</h2>
<svg class="arrow" style="left:19px;top:3589px" viewBox="0 0 56 56"><circle cx="28" cy="28" r="25" fill="none" stroke="#666" stroke-width="3"/><path d="M32 16 L20 28 L32 40" fill="none" stroke="#666" stroke-width="3"/></svg>
<div class="shot" style="left:120px;background:linear-gradient(180deg,#9fb4c9,#d7dfe6 70%,#b7ad92)" role="img" aria-label="Helicopter flying over open ground with parachutist below"></div>
<div class="shot" style="left:366px;background:linear-gradient(180deg,#4f5a3a,#6c7a45)" role="img" aria-label="Operators studying a map on grass"></div>
<div class="shot" style="left:611px;background:linear-gradient(180deg,#7d8a6e,#55683b)" role="img" aria-label="Helicopter landing on a grassy slope with operators"></div>
<div class="shot" style="left:857px;background:linear-gradient(180deg,#4a4a48,#6b5e4c)" role="img" aria-label="Operators with radio equipment at dusk"></div>
<svg class="arrow" style="left:1125px;top:3589px" viewBox="0 0 56 56"><circle cx="28" cy="28" r="25" fill="none" stroke="var(--blue)" stroke-width="3"/><path d="M24 16 L36 28 L24 40" fill="none" stroke="var(--blue)" stroke-width="3"/></svg>

<section class="abs footer"></section>
<svg class="abs" style="left:0;top:4080px" width="1200" height="110" viewBox="0 0 1200 110">
  <path d="M0 40 C300 10 500 20 700 55 C900 90 1050 60 1200 25 L1200 110 L0 110Z" fill="var(--blue)"/>
  <path d="M0 70 C300 40 500 50 700 85 C900 110 1050 90 1200 60 L1200 110 L0 110Z" fill="var(--black)"/>
</svg>
<div class="abs contact-photo" role="img" aria-label="Silhouetted team walking from tiltrotor aircraft at sunset"></div>
<svg class="abs" style="left:45px;top:4238px" width="90" height="75" viewBox="0 0 90 75">
  <g fill="#fff">
    <circle cx="3" cy="3" r="2"/><circle cx="15" cy="3" r="2"/><circle cx="3" cy="15" r="2"/><circle cx="15" cy="15" r="2"/>
    <circle cx="3" cy="27" r="2"/><circle cx="15" cy="27" r="2"/><circle cx="27" cy="27" r="2"/><circle cx="39" cy="27" r="2"/><circle cx="51" cy="27" r="2"/><circle cx="63" cy="27" r="2"/><circle cx="75" cy="27" r="2"/>
    <circle cx="3" cy="39" r="2"/><circle cx="15" cy="39" r="2"/><circle cx="27" cy="39" r="2"/><circle cx="39" cy="39" r="2"/><circle cx="51" cy="39" r="2"/><circle cx="63" cy="39" r="2"/><circle cx="75" cy="39" r="2"/>
  </g>
</svg>
<div class="abs contact-frame"></div>
<form class="abs contact-card">
  <h2 class="contact-title">CONTACT US</h2>
  <div class="field" style="left:30px;top:130px;width:256px">Your Name</div>
  <div class="field" style="left:315px;top:130px;width:256px">Last Name</div>
  <div class="field" style="left:30px;top:198px;width:541px">Email</div>
  <div class="field" style="left:34px;top:262px;width:470px;padding-bottom:40px">Message</div>
  <div class="send"><svg width="32" height="32" viewBox="0 0 24 24"><path d="M3 11 L21 3 L14 21 L11 13Z M11 13 L21 3" fill="none" stroke="#fff" stroke-width="1.6" stroke-linejoin="round"/></svg></div>
</form>

<div class="abs footer-brand"><span class="footer-dot"></span><span class="footer-name">VELMOTRAIL</span></div>
<div class="abs socials"><span class="social"></span><span class="social"></span><span class="social"></span><span class="social"></span></div>
<nav class="abs footer-nav"><span>Mission</span><span>What We Provide</span><span>Map</span><span>Qualifications</span><span>Contact</span><span>Gallery</span></nav>
<div class="abs footer-rule"></div>
<p class="abs copyright">© 2024 VELMOTRAIL I All Rights Reserved</p>

</body>
</html>
```